Stationary Set Rebrand for Brennick

We are a Canadian Distribution and Service Company that was established in 1969. Over the past 5 decades we have expanded our business and have warehouses across Canada. We specialize in adhesive tapes, adhesives, films, safety, warehouse, shipping, janitorial and packaging supplies.

We have updated our logo design and would like a new corporate branding identity that includes a new fresh Stationary Set (Business Cards, Letterhead, Letterhead MS Word, Envelope, Presentation Folders, Email Signatures, Notepad Covers, etc.)

Target Market(s)

Industrial Business Sector

Font styles to use
Sans Serif

Colors
0054AA
0677BA
7BADD7
CADEEF
E8F1F8
0094D4
00A9DD
6FCCEA
C7EBF8
E9F6FB
00AB8E
00BBA5
67D7C9
C6EFE9
E9F9F6
EB3D1F
EC4F4E
F09395
F8D3D4
FCEDEE

Requirements
Should not have
• Colors not too light, darker colours preferred

```html
<!DOCTYPE html>
<html lang="en">
<head>
<meta charset="utf-8">
<title>Brennick Stationery Set</title>
<link rel="stylesheet" href="https://fonts.googleapis.com/css2?family=Roboto:wght@400;700;900&display=swap">
<style>
:root{
  --red:#D9262B;
  --red-dark:#A8161B;
  --red-soft:#EC4F4E;
  --ink:#1A1A1A;
  --grey:#6B6B6B;
  --rule:#BDBDBD;
  --paper:#FFFFFF;
  --board:#E4E4E4;
}
*{box-sizing:border-box;margin:0;padding:0}
html,body{width:703px;height:1200px;overflow:hidden}
body{background:var(--board);font-family:"Roboto",Arial,sans-serif;color:var(--ink);position:relative}
.item{position:absolute;background:var(--paper);box-shadow:0 2px 6px rgba(0,0,0,.18);overflow:hidden}
.brand{font-family:"Roboto",Arial,sans-serif;font-weight:900;color:var(--ink);line-height:1;letter-spacing:-.5px;white-space:nowrap}
.brand--light{color:var(--paper)}
.head-rule{position:absolute;left:0;height:3px;background:var(--red)}
.head-rule::after{content:"";position:absolute;left:0;right:0;top:5px;height:1px;background:var(--ink)}

/* business card */
.card-front{left:40px;top:25px;width:300px;height:170px}
.card-front .brand{position:absolute;right:16px;top:14px;font-size:26px}
.card-front .head-rule{top:34px;width:155px}
.person{position:absolute;left:18px;top:74px}
.person__name{color:var(--red);font-weight:700;font-size:12px;letter-spacing:.3px}
.person__role{font-size:9px;color:var(--grey);margin-top:2px}
.contacts{position:absolute;left:160px;top:68px;list-style:none;font-size:8.5px;color:var(--grey);line-height:14px}
.contacts li::before{content:"";display:inline-block;width:6px;height:6px;border-radius:50%;background:var(--red);margin-right:5px;vertical-align:0}
.address{position:absolute;left:0;right:0;bottom:14px;text-align:center;font-size:8.5px;color:var(--grey)}

.card-back{left:40px;top:225px;width:300px;height:170px;background:linear-gradient(135deg,var(--red-soft),var(--red) 55%,var(--red-dark))}
.card-back__art{position:absolute;left:30px;top:20px;width:130px;height:130px;border-radius:50%;background:radial-gradient(circle,rgba(255,255,255,.12),rgba(255,255,255,0) 70%)}
.card-back .brand{position:absolute;right:22px;top:62px;font-size:34px}
.card-back__rule{position:absolute;right:22px;top:104px;width:150px;height:2px;background:var(--paper)}

/* envelopes */
.env-front{left:363px;top:25px;width:300px;height:170px}
.env-front .brand{position:absolute;right:14px;top:12px;font-size:20px}
.env-front .head-rule{top:29px;width:185px}
.env-front__return{position:absolute;left:14px;top:42px;font-size:5.5px;color:var(--grey);line-height:8px}
.env-back{left:363px;top:225px;width:300px;height:170px}
.env-back svg{position:absolute;inset:0}
.env-back .brand{position:absolute;left:0;right:0;top:22px;text-align:center;font-size:22px}

/* letterhead */
.sheet{width:200px;height:283px}
.sheet .brand{position:absolute;right:12px;top:12px;font-size:16px}
.sheet .head-rule{top:25px;width:calc(100% - 92px);height:2px}
.sheet .head-rule::after{top:4px}
.sheet__body{position:absolute;left:16px;right:16px;top:50px;font-size:4.5px;line-height:7px;color:#444}
.sheet__body p{margin-bottom:6px}
.sheet__foot{position:absolute;left:0;right:0;bottom:10px;height:2px;background:var(--red)}
.letterhead{left:40px;top:420px}

/* notepad */
.notepad{left:40px;top:740px}
.notepad__lines{position:absolute;left:16px;right:16px;top:44px;bottom:24px;background:repeating-linear-gradient(to bottom,transparent 0 11px,#D6D6D6 11px 12px)}

/* folder cover */
.folder-cover{left:262px;top:420px;width:401px;height:283px;background:none;box-shadow:none;overflow:visible}
.folder-cover__front{position:absolute;left:0;top:0;width:200px;height:283px;background:linear-gradient(150deg,var(--red-soft),var(--red) 50%,var(--red-dark));box-shadow:0 2px 6px rgba(0,0,0,.18)}
.folder-cover__front .brand{position:absolute;right:14px;top:26px;font-size:30px}
.folder-cover__art{position:absolute;left:20px;top:90px;width:150px;height:170px;border-radius:50%;background:radial-gradient(circle,rgba(255,255,255,.14),rgba(255,255,255,0) 70%)}
.folder-cover__inside{position:absolute;left:200px;top:0;width:201px;height:283px;background:#F4F4F4;box-shadow:0 2px 6px rgba(0,0,0,.18)}
.folder-cover__inside .sheet{position:absolute;left:10px;top:0;height:283px;box-shadow:-2px 0 4px rgba(0,0,0,.12)}

/* folder inside */
.folder-open{left:262px;top:740px;width:401px;height:283px}
.folder-open__panel{position:absolute;top:0;width:200px;height:283px;background:var(--paper)}
.folder-open__panel--left{left:0;border-right:1px solid #DDD}
.folder-open__panel--right{left:201px}
.folder-open svg{position:absolute;left:0;bottom:0}
.folder-open .sheet{position:absolute;left:216px;top:22px;width:172px;height:200px;box-shadow:0 1px 4px rgba(0,0,0,.2)}

/* email signature */
.signature{left:80px;top:1045px;width:543px;height:140px}
.signature .brand{position:absolute;right:24px;top:10px;font-size:38px}
.signature .head-rule{top:52px;width:320px;height:4px}
.signature .head-rule::after{top:7px;height:1.5px}
.signature .person{left:28px;top:74px}
.signature .person__name{font-size:16px}
.signature .person__role{font-size:12px}
.signature .contacts{left:300px;top:68px;font-size:11px;line-height:15px}
.signature .contacts li::before{width:8px;height:8px}
.signature .address{bottom:8px;left:0;right:0;text-align:center;font-size:11px}
</style>
</head>
<body>

<section class="item card-front" aria-label="Business card front">
  <div class="head-rule"></div>
  <div class="brand">Brennick</div>
  <div class="person">
    <div class="person__name">MARCUS HALE</div>
    <div class="person__role">Managing Director</div>
  </div>
  <ul class="contacts">
    <li>044-555 210 987</li>
    <li>hello@brennick-supply.com</li>
    <li>www.brennick-supply.com</li>
  </ul>
  <div class="address">Your Address, City, State, Zip 0000</div>
</section>

<section class="item env-front" aria-label="Envelope front">
  <div class="head-rule"></div>
  <div class="brand">Brennick</div>
  <div class="env-front__return">12 Dock Road, Toronto ON</div>
</section>

<section class="item card-back" aria-label="Business card back">
  <div class="card-back__art" role="img" aria-label="Soft decorative glow area"></div>
  <div class="brand brand--light">Brennick</div>
  <div class="card-back__rule"></div>
</section>

<section class="item env-back" aria-label="Envelope back">
  <svg width="300" height="170" viewBox="0 0 300 170">
    <polyline points="0,0 150,78 300,0" fill="none" stroke="#CFCFCF" stroke-width="1.2"/>
    <polyline points="0,170 118,70" fill="none" stroke="#E2E2E2" stroke-width="1"/>
    <polyline points="300,170 182,70" fill="none" stroke="#E2E2E2" stroke-width="1"/>
  </svg>
  <div class="brand">Brennick</div>
</section>

<section class="item sheet letterhead" aria-label="Letterhead">
  <div class="head-rule"></div>
  <div class="brand">Brennick</div>
  <div class="sheet__body">
    <p>Dear Ms. Carter,</p>
    <p>Thank you for choosing us for your tape and packaging supply needs. Our team ships across the country from regional warehouses every week.</p>
    <p>Thank you for choosing us for your tape and packaging supply needs. Our team ships across the country from regional warehouses every week.</p>
    <p>Sincerely,</p>
  </div>
  <div class="sheet__foot"></div>
</section>

<section class="item folder-cover" aria-label="Presentation folder cover">
  <div class="folder-cover__front">
    <div class="folder-cover__art" role="img" aria-label="Soft tonal decoration on folder cover"></div>
    <div class="brand brand--light">Brennick</div>
  </div>
  <div class="folder-cover__inside">
    <div class="item sheet">
      <div class="head-rule"></div>
      <div class="brand">Brennick</div>
      <div class="sheet__foot"></div>
    </div>
  </div>
</section>

<section class="item sheet notepad" aria-label="Notepad">
  <div class="head-rule"></div>
  <div class="brand">Brennick</div>
  <div class="notepad__lines"></div>
  <div class="sheet__foot"></div>
</section>

<section class="item folder-open" aria-label="Presentation folder inside">
  <div class="folder-open__panel folder-open__panel--left"></div>
  <div class="folder-open__panel folder-open__panel--right"></div>
  <div class="item sheet">
    <div class="head-rule"></div>
    <div class="brand">Brennick</div>
    <div class="sheet__body">
      <p>Dear Ms. Carter,</p>
      <p>Thank you for choosing us for your tape and packaging supply needs. Our team ships across the country from regional warehouses every week.</p>
      <p>Thank you for choosing us for your tape and packaging supply needs. Our team ships across the country from regional warehouses every week.</p>
      <p>Sincerely,</p>
    </div>
  </div>
  <svg width="401" height="120" viewBox="0 0 401 120">
    <path d="M0 30 L150 30 Q175 30 185 120 L0 120 Z" fill="var(--red)"/>
    <path d="M401 30 L251 30 Q226 30 216 120 L401 120 Z" fill="var(--red)"/>
    <line x1="200.5" y1="0" x2="200.5" y2="120" stroke="var(--red-dark)" stroke-width="1"/>
  </svg>
</section>

<section class="item signature" aria-label="Email signature">
  <div class="head-rule"></div>
  <div class="brand">Brennick</div>
  <div class="person">
    <div class="person__name">MARCUS HALE</div>
    <div class="person__role">Managing Director</div>
  </div>
  <ul class="contacts">
    <li>044-555 210 987</li>
    <li>hello@brennick-supply.com</li>
    <li>www.brennick-supply.com</li>
  </ul>
  <div class="address">Your Address, City, State, Zip 0000</div>
</section>

</body>
</html>
```